Coastline Premier Retreats Business Card Design

Design a business card for Coastline Premier Retreats. Look at the website for colors and reference. Card should have logo, name, title, office number, mobile number, email, URL and a tagline like, "Luxury Hotel & Resort Email Marketing" (This might change).

https://www.coastlinepremierretreats.example

The rest I will leave up to your imagination.

Contact Information for Business Card

Logo, name, title, office number, mobile number, email, URL and a tagline like, "Luxury Hotel & Resort Email Marketing" (This might change).

```html
<!DOCTYPE html>
<html lang="en">
<head>
<meta charset="utf-8">
<title>Coastline Premier Retreats – Business Card</title>
<link rel="stylesheet" href="https://fonts.googleapis.com/css2?family=Roboto:wght@400;500;900&display=swap">
<style>
  :root {
    --bg: #e6e6e6;
    --card-white: #f6f6f7;
    --brand-orange: #e56b05;
    --ink: #141414;
    --ink-soft: #6f6f6f;
    --rule: #2a2a2a;
  }
  * { margin: 0; padding: 0; box-sizing: border-box; }
  html, body {
    width: 1200px; height: 960px; overflow: hidden;
    background: var(--bg);
    font-family: "Roboto", Arial, sans-serif;
    color: var(--ink);
  }
  .canvas { position: relative; width: 1200px; height: 960px; }

  .card {
    position: absolute; left: 250px;
    width: 700px; height: 400px;
    border-radius: 26px;
    overflow: hidden;
    box-shadow: 0 6px 18px rgba(0,0,0,0.18);
  }

  /* Front */
  .card-front { top: 40px; background: var(--card-white); }
  .brand-name {
    position: absolute; left: 150px; top: 58px;
    font-weight: 900; font-size: 30px; letter-spacing: 0.5px;
    color: var(--ink); text-transform: uppercase;
  }
  .accent-tab {
    position: absolute; left: 0; top: 150px;
    width: 32px; height: 32px; background: var(--brand-orange);
  }
  .person { position: absolute; left: 98px; top: 146px; }
  .person-name { font-weight: 900; font-size: 27px; line-height: 1; }
  .person-title { font-size: 17px; color: var(--ink-soft); margin-top: 3px; }
  .name-rule {
    position: absolute; left: 88px; top: 200px;
    width: 560px; height: 1.5px; background: var(--rule);
  }
  .contacts {
    position: absolute; left: 88px; top: 214px;
    display: flex; align-items: stretch;
  }
  .contact-group { display: flex; flex-direction: column; gap: 6px; }
  .contact-group.phones { padding-right: 18px; border-right: 1.5px solid var(--rule); }
  .contact-group.online { padding-left: 18px; }
  .contact-line {
    display: flex; align-items: center; gap: 8px;
    font-size: 18px; line-height: 1.15;
  }
  .contact-line svg { width: 15px; height: 15px; flex: none; }
  .tagline {
    position: absolute; left: 88px; top: 290px;
    font-size: 18px;
  }
  .bottom-rule {
    position: absolute; left: 88px; top: 322px;
    width: 560px; height: 1.5px; background: var(--rule);
  }

  /* Back */
  .card-back {
    top: 500px; background: var(--brand-orange);
    display: flex; align-items: center; justify-content: center;
  }
  .back-brand {
    font-weight: 900; font-size: 40px; letter-spacing: 1px;
    color: #f2b04a; text-transform: uppercase;
  }
</style>
</head>
<body>
<main class="canvas">

  <section class="card card-front" aria-label="Business card front">
    <div class="brand-name">Coastline Premier Retreats</div>
    <div class="accent-tab"></div>
    <div class="person">
      <div class="person-name">Daniel Reyes</div>
      <div class="person-title">President</div>
    </div>
    <div class="name-rule"></div>
    <div class="contacts">
      <div class="contact-group phones">
        <div class="contact-line">
          <svg viewBox="0 0 16 16" aria-hidden="true"><path fill="#e56b05" d="M3.6 1.2l2.3 2.6-1.4 1.8c.9 2 2.4 3.6 4.4 4.6l1.8-1.4 2.6 2.3-1.3 2.4C6.6 13.4 2.6 9.4 1.3 3.8z"/></svg>
          <span>555.014.2000</span>
        </div>
        <div class="contact-line">
          <svg viewBox="0 0 16 16" aria-hidden="true"><rect x="4" y="1" width="8" height="14" rx="1.5" fill="none" stroke="#e56b05" stroke-width="1.8"/><rect x="7" y="12" width="2" height="1.4" fill="#e56b05"/></svg>
          <span>555.014.2001</span>
        </div>
      </div>
      <div class="contact-group online">
        <div class="contact-line">
          <svg viewBox="0 0 16 16" aria-hidden="true"><rect x="1" y="3" width="14" height="10" fill="#e56b05"/><path d="M1.5 3.5L8 9l6.5-5.5" fill="none" stroke="#fff" stroke-width="1.3"/></svg>
          <span>info@coastlinepremierretreats.example</span>
        </div>
        <div class="contact-line">
          <svg viewBox="0 0 16 16" aria-hidden="true"><circle cx="8" cy="8" r="7" fill="#e56b05"/><path d="M1 8h14M8 1c-3 3-3 11 0 14M8 1c3 3 3 11 0 14" fill="none" stroke="#fff" stroke-width="1"/></svg>
          <span>www.coastlinepremierretreats.example</span>
        </div>
      </div>
    </div>
    <div class="tagline">Luxury Hotel &amp; Resort Email Marketing</div>
    <div class="bottom-rule"></div>
  </section>

  <section class="card card-back" aria-label="Business card back">
    <div class="back-brand">Coastline Premier Retreats</div>
  </section>

</main>
</body>
</html>
```